Harborline Claim Advocates Business card

We need to get business card Design for our Company we are Public Adjusters in Chicago Illinois - i like to see good combination and elements from my Company Logo. as well To be an two side design
Updates

Target Market(s)

Home /Business owner Property Managers

Industry/Entity Type

Business

Contact Information for Business Card

to show the Element of our logo i will Like 3D

Font styles to use
Sans Serif

Requirements
Must have
• Logo and Element of the Logo in 3D
Nice to have
• Logo That we Provide 3D Same Colors or open for suggestions
Should not have
• unleare view -

```html
<!DOCTYPE html>
<html lang="en">
<head>
<meta charset="utf-8">
<title>Harborline Claim Advocates — Stationery</title>
<link href="https://fonts.googleapis.com/css2?family=Lato:wght@400;700;900&display=swap" rel="stylesheet">
<style>
  :root{
    --bg:#eceef0;
    --paper:#ffffff;
    --ink:#3b3f48;
    --muted:#7a7f8a;
    --navy:#1c2466;
    --blue:#1f4fc6;
    --deep:#141b4f;
    --red:#c4161c;
    --rule:#d9dce2;
    --folder-text:#5f86e8;
  }
  *{box-sizing:border-box;margin:0;padding:0}
  html,body{width:1200px;height:795px;overflow:hidden}
  body{background:var(--bg);font-family:'Lato',sans-serif;color:var(--ink);position:relative}
  .sheet{position:absolute;background:var(--paper);box-shadow:0 2px 8px rgba(0,0,0,.12)}
  .brand{display:flex;align-items:center;gap:6px;font-weight:700;color:var(--navy);white-space:nowrap}
  .brand-dot{border-radius:50%;background:var(--navy);flex:none}
  .stripe{position:absolute;left:0;right:0;bottom:0;display:flex}
  .stripe .blue{flex:3;background:linear-gradient(90deg,var(--navy),var(--blue),var(--navy))}
  .stripe .red{flex:1;background:var(--red)}

  /* Letterhead */
  .letterhead{left:330px;top:30px;width:310px;height:420px;padding:26px 26px 0}
  .letterhead .brand{font-size:10px}
  .letterhead .brand-dot{width:12px;height:12px}
  .letterhead .sender{position:absolute;right:26px;top:62px;width:72px;text-align:right;font-size:5.5px;line-height:1.6;color:var(--muted)}
  .letterhead .salutation{margin-top:42px;font-size:8px}
  .letterhead .body{width:172px;margin-top:10px;font-size:5.5px;line-height:1.65;color:var(--muted)}
  .letterhead .body p+p{margin-top:8px}
  .letterhead .closing{margin-top:16px;font-size:6.5px}
  .letterhead .closing small{display:block;font-size:5px;color:var(--muted);margin-top:2px}
  .signature{width:60px;height:16px;margin-top:8px;background:linear-gradient(90deg,#e4e6ea,#f4f5f7);border-radius:3px}
  .letterhead .stripe{height:7px}

  /* Folder */
  .folder{left:680px;top:30px;width:360px;height:440px;background:radial-gradient(circle at 55% 45%,var(--blue) 0%,#1a3596 38%,var(--deep) 80%);overflow:hidden}
  .folder .spine{position:absolute;left:0;top:0;bottom:0;width:16px;background:var(--red)}
  .folder .brand{position:absolute;left:16px;right:0;top:190px;justify-content:center;font-size:17px;color:var(--folder-text)}
  .folder .brand-dot{width:22px;height:22px;background:var(--folder-text)}

  /* Envelopes */
  .envelope{left:290px;top:490px;width:440px;height:220px;padding:20px 24px}
  .envelope .brand{font-size:9px}
  .envelope .brand-dot{width:12px;height:12px}
  .envelope address{font-style:normal;font-size:5.5px;line-height:1.6;color:var(--muted);margin-top:6px}
  .envelope .stripe{height:7px}
  .envelope-back{left:770px;top:500px;width:400px;height:210px;overflow:hidden}
  .envelope-back svg{position:absolute;inset:0}

  /* Business cards */
  .card{width:220px;height:125px;overflow:hidden}
  .card-front{left:40px;top:480px;padding:18px 14px;display:flex;gap:10px}
  .card-front .brand{font-size:8.5px;width:86px;flex-direction:column;align-items:flex-start;gap:5px;line-height:1.25;white-space:normal}
  .card-front .brand-dot{width:16px;height:16px}
  .card-front .divider{width:1px;background:var(--rule);height:70px;flex:none}
  .card-front .details{flex:1;min-width:0}
  .card-front .person{font-size:7px;font-weight:900;color:var(--navy);letter-spacing:.04em}
  .card-front .role{font-size:5.5px;color:var(--red);margin-bottom:6px}
  .card-front ul{list-style:none;font-size:5.2px;color:var(--muted);line-height:1.9}
  .card-front li{display:flex;align-items:center;gap:4px;white-space:nowrap}
  .card-front li svg{width:6px;height:6px;flex:none}
  .card-front .stripe{height:6px}
  .card-back{left:40px;top:625px;background:radial-gradient(circle at 50% 40%,var(--blue),var(--deep) 85%);display:flex;flex-direction:column;align-items:center;justify-content:center;gap:10px}
  .card-back .brand{font-size:10px;color:#fff}
  .card-back .brand-dot{width:14px;height:14px;background:#fff}
  .card-back .web{font-size:6px;color:#c9d4f5;letter-spacing:.08em}
</style>
</head>
<body>

<section class="sheet letterhead">
  <div class="brand"><span class="brand-dot"></span>Harborline Claim Advocates</div>
  <div class="sender">
    1180 Lakeview Row<br>Chicago, IL 60601<br>312 555 0148<br>312 555 0149<br>hello@harborline.co<br>www.harborline.co
  </div>
  <p class="salutation">Dear Mr. Hale,</p>
  <div class="body">
    <p>Thank you for choosing our team to review your property claim. We study every policy line, document the damage with care and present a clear estimate to your insurer. Our aim is a fair settlement reached quickly, so you can return to your home or business with confidence.</p>
    <p>Please keep copies of receipts, photos and repair quotes. We will contact you within two business days to plan the inspection and answer any questions you may have about the next steps.</p>
  </div>
  <p class="closing">Dana Reyes<small>Co-Founder &amp; CEO</small></p>
  <div class="signature" role="img" aria-label="Handwritten signature"></div>
  <div class="stripe"><span class="blue"></span><span class="red"></span></div>
</section>

<section class="sheet folder">
  <div class="spine"></div>
  <div class="brand"><span class="brand-dot"></span>Harborline Claim Advocates</div>
</section>

<section class="sheet card card-front">
  <div class="brand"><span class="brand-dot"></span>Harborline Claim Advocates</div>
  <div class="divider"></div>
  <div class="details">
    <p class="person">DANA REYES</p>
    <p class="role">Claim Advocate</p>
    <ul>
      <li><svg viewBox="0 0 10 10"><path d="M2 1l2 0 1 2-1 1c1 1 1 2 2 2l1-1 2 1 0 2c-4 0-7-3-7-7z" fill="#1c2466"/></svg>312 555 0148</li>
      <li><svg viewBox="0 0 10 10"><path d="M5 0a3.5 3.5 0 0 1 3.5 3.5C8.5 6 5 10 5 10S1.5 6 1.5 3.5A3.5 3.5 0 0 1 5 0z" fill="#1c2466"/><circle cx="5" cy="3.5" r="1.2" fill="#fff"/></svg>1180 Lakeview Row</li>
      <li><svg viewBox="0 0 10 10"><rect x="0.5" y="2" width="9" height="6" fill="#1c2466"/><path d="M0.5 2l4.5 3.5L9.5 2" stroke="#fff" fill="none"/></svg>hello@harborline.co</li>
      <li><svg viewBox="0 0 10 10"><circle cx="5" cy="5" r="4.2" fill="none" stroke="#1c2466"/><path d="M0.8 5h8.4M5 .8c-2 2.5-2 5.9 0 8.4M5 .8c2 2.5 2 5.9 0 8.4" stroke="#1c2466" fill="none" stroke-width=".7"/></svg>www.harborline.co</li>
    </ul>
  </div>
  <div class="stripe"><span class="blue"></span><span class="red"></span></div>
</section>

<section class="sheet card card-back">
  <div class="brand"><span class="brand-dot"></span>Harborline Claim Advocates</div>
  <p class="web">www.harborline.co</p>
</section>

<section class="sheet envelope">
  <div class="brand"><span class="brand-dot"></span>Harborline Claim Advocates</div>
  <address>1180 Lakeview Row<br>Chicago, IL 60601</address>
  <div class="stripe"><span class="blue"></span><span class="red"></span></div>
</section>

<section class="sheet envelope-back">
  <svg viewBox="0 0 400 210" preserveAspectRatio="none">
    <rect width="400" height="210" fill="#fff"/>
    <path d="M8 8 H392 L382 60 H18 Z" fill="#f5f6f8" stroke="#dfe2e7"/>
  </svg>
</section>

</body>
</html>
```